Edit and Update existing catalog

I have a 60 paged catalog that needs to have some changes. We are adding around 20 pages, changing another 15 pages, and also have 10 pages that need to be graphically designed and inserted. The current existing catalog is included as well as a PDF explaining all the changes (Catalog Changes.pdf), as well as all the pages that need to be added and our logo.

Target Market(s)

physician offices and professional healthcare providers

Industry/Entity Type

Healthcare

Colors
0054AA
0677BA
7BADD7
CADEEF
E8F1F8

Requirements
Must have
• Additional pages must match the format of the existing catalog
Should not have
• No protected health information - all patient names, Date of births and accession #s should be removed, incase they are not please replace with XXX on the reports.

```html
<!DOCTYPE html>
<html lang="en">
<head>
<meta charset="utf-8">
<title>Meridian Labs – Catalog Spreads Overview</title>
<link href="https://fonts.googleapis.com/css2?family=Montserrat:wght@600;700;800&family=Open+Sans:wght@400;600;700&display=swap" rel="stylesheet">
<style>
:root{
  --bg:#f5901f;
  --blue-dark:#0054aa;
  --blue-mid:#0677ba;
  --blue-soft:#7badd7;
  --blue-pale:#cadeef;
  --blue-mist:#e8f1f8;
  --ink:#3a3f47;
  --line:#b9c2cc;
  --edge:#2b2e33;
  --white:#ffffff;
  --red:#d9362b;
  --yellow:#f2c623;
}
*{box-sizing:border-box;margin:0;padding:0}
html,body{width:1200px;height:1000px;overflow:hidden}
body{background:var(--bg);font-family:"Open Sans",sans-serif;position:relative;color:var(--ink)}
.spread{position:absolute;width:210px;height:128px;display:flex;background:var(--white);border-left:3px solid var(--edge);border-right:3px solid var(--edge)}
.page{position:relative;width:50%;height:100%;overflow:hidden;background:var(--white)}
.page + .page{border-left:3px solid var(--edge)}
.abs{position:absolute}
.copy{position:absolute;background:repeating-linear-gradient(to bottom,var(--line) 0 1px,transparent 1px 3px)}
.copy.dense{background:repeating-linear-gradient(to bottom,#8e98a3 0 1px,transparent 1px 2.5px)}
.grid{position:absolute;border:0.5px solid var(--blue-soft);background:
  repeating-linear-gradient(to bottom,var(--blue-pale) 0 0.6px,transparent 0.6px 3px),
  repeating-linear-gradient(to right,var(--blue-pale) 0 0.6px,transparent 0.6px 16px)}
.grid.blue-head{border-top:3px solid var(--blue-dark)}
.bar{position:absolute;background:var(--blue-dark)}
.mini{position:absolute;font-size:3.2px;line-height:1.2;color:var(--ink);white-space:nowrap}
.hd{position:absolute;z-index:2;font-family:"Montserrat",sans-serif;font-weight:700;color:var(--blue-dark);line-height:1.05}
.brand{position:absolute;z-index:2;display:flex;align-items:center;gap:2px;font-family:"Open Sans",sans-serif;font-weight:700;font-size:3.6px;color:var(--blue-dark);letter-spacing:.2px;white-space:nowrap}
.brand .dot{width:5px;height:5px;border-radius:50%;background:var(--blue-dark)}
.photo{position:absolute;z-index:1;background:linear-gradient(150deg,var(--blue-mist),var(--blue-soft) 55%,#6d8fae)}
.photo.warm{background:linear-gradient(150deg,#f1e3d6,#c9a48a 55%,#7d8ea3)}
.photo.lab{background:linear-gradient(160deg,#dfe9f2,#9fb9d0 60%,#52708f)}
.cover-band{position:absolute;left:0;top:0;width:100%;height:100%}
.cover-mark{position:absolute;z-index:2;left:6px;top:9px;width:13px;height:13px;border-radius:50%;border:1.2px solid var(--white)}
.cover-name{position:absolute;z-index:2;left:6px;top:24px;font-weight:700;font-size:3.4px;color:var(--white)}
.tab{position:absolute;right:0;top:0;width:5px;height:100%;background:var(--blue-dark)}
.cover-title{position:absolute;z-index:2;font-family:"Montserrat",sans-serif;font-weight:700;color:var(--blue-mid);line-height:1;white-space:nowrap}
.vt{position:absolute;writing-mode:vertical-rl;transform:rotate(180deg);font-family:"Montserrat",sans-serif;font-weight:800;color:var(--blue-mid);white-space:nowrap}
.rotate-guide{position:absolute;display:flex;flex-direction:column;gap:1px}
.swatch{height:6px;width:100%}
.contact-word{position:absolute;z-index:2;font-family:"Montserrat",sans-serif;font-weight:800;font-size:10px;color:var(--white);letter-spacing:.3px}
</style>
</head>
<body>

<!-- Row 1 -->
<div class="spread" style="left:39px;top:83px">
  <div class="page">
    <div class="brand" style="left:36px;top:14px"><span class="dot"></span>MERIDIAN LABS</div>
    <div class="mini" style="left:34px;top:22px;color:var(--blue-mid)">CLIA ID: 00X0000</div>
    <div class="copy" style="left:10px;top:30px;width:64px;height:16px"></div>
    <div class="copy" style="left:14px;top:50px;width:56px;height:36px"></div>
    <div class="mini" style="left:10px;top:112px;color:var(--blue-mid)">410 Harbor Ridge Dr · Lakeview</div>
  </div>
  <div class="page"></div>
</div>

<div class="spread" style="left:267px;top:83px">
  <div class="page"></div>
  <div class="page">
    <svg class="cover-band" viewBox="0 0 100 128" preserveAspectRatio="none"><polygon points="0,0 100,0 100,14 0,44" fill="var(--blue-dark)"/><polygon points="0,44 100,14 100,18 0,48" fill="var(--blue-mid)"/></svg>
    <span class="cover-mark"></span><span class="cover-name">MERIDIAN</span>
    <div class="tab" style="top:20px;height:80px"></div>
    <div class="cover-title" style="left:21px;top:52px;font-size:7.4px">Clinical<br>Laboratory<br><span style="font-size:6px;letter-spacing:.5px">SERVICES</span></div>
    <div class="photo" role="img" aria-label="Nurse drawing a blood sample from a patient's arm" style="left:30px;top:80px;width:65px;height:48px;clip-path:polygon(30% 0,100% 0,100% 100%,0 100%)"></div>
  </div>
</div>

<div class="spread" style="left:497px;top:83px">
  <div class="page">
    <div class="brand" style="left:5px;top:8px"><span class="dot"></span>MERIDIAN</div>
    <div class="hd" style="left:44px;top:8px;font-size:3.2px">Pharmacogenomic (PGx)<br>Drug Response Testing</div>
    <div class="copy" style="left:5px;top:22px;width:32px;height:34px"></div>
    <div class="bar" style="left:5px;top:58px;width:32px;height:4px;background:var(--blue-pale)"></div>
    <svg class="abs" style="left:12px;top:66px" width="22" height="22" viewBox="0 0 20 20"><circle cx="10" cy="10" r="9" fill="var(--blue-pale)"/><path d="M10 10 L10 1 A9 9 0 0 1 19 10Z" fill="var(--blue-dark)"/></svg>
    <div class="copy" style="left:44px;top:20px;width:20px;height:30px"></div>
    <div class="copy" style="left:70px;top:20px;width:22px;height:60px"></div>
    <div class="photo" role="img" aria-label="Row of pill and patient icons" style="left:44px;top:56px;width:22px;height:56px;background:linear-gradient(var(--blue-mist),var(--blue-pale))"></div>
  </div>
  <div class="page">
    <div class="brand" style="left:52px;top:6px"><span class="dot"></span>MERIDIAN</div>
    <div class="hd" style="left:5px;top:17px;font-size:3.4px;color:#1f2a37;width:44px">Postpartum PGx benefits</div>
    <div class="copy dense" style="left:5px;top:25px;width:42px;height:34px"></div>
    <div class="photo warm" role="img" aria-label="Mother holding her infant" style="left:52px;top:15px;width:42px;height:44px"></div>
    <div class="hd" style="left:5px;top:64px;font-size:2.8px;color:#1f2a37;white-space:nowrap">How PGx testing helps with postpartum depression</div>
    <div class="copy dense" style="left:5px;top:70px;width:88px;height:44px"></div>
  </div>
</div>

<div class="spread" style="left:725px;top:83px">
  <div class="page"></div>
  <div class="page">
    <div class="brand" style="left:5px;top:6px"><span class="dot"></span>MERIDIAN</div>
    <div class="grid" style="left:5px;top:17px;width:88px;height:10px"></div>
    <div class="copy" style="left:5px;top:30px;width:34px;height:44px"></div>
    <div class="copy" style="left:45px;top:30px;width:48px;height:18px"></div>
    <div class="copy" style="left:5px;top:80px;width:88px;height:28px"></div>
  </div>
</div>

<div class="spread" style="left:950px;top:83px">
  <div class="page"></div>
  <div class="page">
    <div class="brand" style="left:5px;top:6px"><span class="dot"></span>MERIDIAN</div>
    <div class="grid" style="left:5px;top:16px;width:88px;height:8px"></div>
    <div class="grid" style="left:5px;top:27px;width:88px;height:26px"></div>
    <div class="copy" style="left:5px;top:57px;width:40px;height:10px"></div>
    <div class="copy" style="left:50px;top:57px;width:43px;height:10px"></div>
  </div>
</div>

<!-- Row 2 -->
<div class="spread" style="left:39px;top:227px">
  <div class="page"></div>
  <div class="page">
    <svg class="cover-band" viewBox="0 0 100 128" preserveAspectRatio="none"><polygon points="0,0 100,0 100,20 0,40" fill="var(--blue-dark)"/><polygon points="0,40 100,20 100,24 0,44" fill="var(--blue-mid)"/></svg>
    <span class="cover-mark"></span><span class="cover-name">MERIDIAN</span>
    <div class="tab" style="top:28px;height:70px"></div>
    <div class="cover-title" style="left:12px;top:48px;font-size:7px">Toxicology</div>
    <div class="mini" style="left:12px;top:56px;font-size:2.4px;color:var(--blue-dark)">URINE AND ORAL FLUID DRUG TESTING</div>
    <div class="photo" role="img" aria-label="Doctor and patient reviewing results on a tablet" style="left:6px;top:64px;width:80px;height:62px"></div>
  </div>
</div>

<div class="spread" style="left:267px;top:227px">
  <div class="page"><div class="tab" style="left:0;width:3px;top:40px;height:50px"></div></div>
  <div class="page">
    <div class="brand" style="left:5px;top:6px"><span class="dot"></span>MERIDIAN</div>
    <div class="hd" style="left:38px;top:7px;font-size:2.6px;white-space:nowrap">BLOOD TEST REQUISITION FORM</div>
    <div class="grid" style="left:5px;top:14px;width:88px;height:20px"></div>
    <div class="bar" style="left:5px;top:36px;width:88px;height:2px;background:var(--red)"></div>
    <div class="copy dense" style="left:5px;top:40px;width:28px;height:80px"></div>
    <div class="copy dense" style="left:35px;top:40px;width:28px;height:80px"></div>
    <div class="copy dense" style="left:65px;top:40px;width:28px;height:80px"></div>
  </div>
</div>

<div class="spread" style="left:497px;top:227px">
  <div class="page">
    <div class="hd" style="left:5px;top:6px;font-size:3.4px;white-space:nowrap">Pharmacogenomic (PGx) Testing</div>
    <div class="copy dense" style="left:5px;top:14px;width:90px;height:12px"></div>
    <div class="copy" style="left:5px;top:30px;width:40px;height:30px"></div>
    <div class="photo" role="img" aria-label="Flow diagram of prescribing with and without PGx testing" style="left:50px;top:30px;width:44px;height:34px;background:linear-gradient(var(--blue-mist),var(--blue-pale))"></div>
    <div class="copy" style="left:5px;top:68px;width:90px;height:48px"></div>
  </div>
  <div class="page">
    <div class="brand" style="left:60px;top:6px"><span class="dot"></span>MERIDIAN</div>
    <div class="grid blue-head" style="left:5px;top:16px;width:88px;height:44px"></div>
    <div class="copy dense" style="left:5px;top:64px;width:88px;height:50px"></div>
  </div>
</div>

<div class="spread" style="left:725px;top:227px">
  <div class="page">
    <div class="photo warm" role="img" aria-label="Group of smiling women" style="left:0;top:0;width:100%;height:58px"></div>
    <span class="abs" style="left:86px;top:4px;width:8px;height:8px;border-radius:50%;background:var(--bg);z-index:2"></span>
    <div class="hd" style="left:5px;top:35px;font-size:4.2px;color:var(--white);white-space:nowrap">Elevate the standard of<br>cervical cancer screening</div>
    <div class="mini" style="left:5px;top:64px;color:var(--red);font-size:2.8px">Individual identification of high-risk genotypes</div>
    <svg class="abs" style="left:6px;top:74px" width="90" height="40" viewBox="0 0 90 40"><g fill="var(--red)"><circle cx="8" cy="6" r="4"/><circle cx="18" cy="6" r="4"/><circle cx="58" cy="6" r="4"/><circle cx="68" cy="6" r="4"/><circle cx="78" cy="6" r="4"/></g><circle cx="13" cy="22" r="9" fill="var(--blue-mid)"/><g fill="var(--blue-mid)"><circle cx="58" cy="18" r="4"/><circle cx="68" cy="18" r="4"/><circle cx="78" cy="18" r="4"/><circle cx="63" cy="30" r="4"/><circle cx="73" cy="30" r="4"/></g></svg>
  </div>
  <div class="page">
    <div class="mini" style="left:5px;top:6px;color:var(--red);font-size:2.8px">CervaScreen HPV Assay now in guidelines</div>
    <div class="grid" style="left:5px;top:14px;width:88px;height:50px;border-color:var(--red)"></div>
    <svg class="abs" style="left:5px;top:68px" width="60" height="40" viewBox="0 0 60 40"><g fill="var(--blue-soft)"><rect x="2" y="8" width="4" height="32"/><rect x="8" y="18" width="4" height="22"/><rect x="14" y="24" width="4" height="16"/><rect x="20" y="28" width="4" height="12"/><rect x="26" y="30" width="4" height="10"/><rect x="32" y="33" width="4" height="7"/><rect x="38" y="35" width="4" height="5"/></g></svg>
    <div class="brand" style="left:5px;top:115px"><span class="dot"></span>MERIDIAN</div>
  </div>
</div>

<div class="spread" style="left:950px;top:227px">
  <div class="page">
    <div class="brand" style="left:5px;top:6px"><span class="dot"></span>MERIDIAN</div>
    <div class="hd" style="left:5px;top:18px;font-size:3.6px;font-family:Georgia,serif;color:var(--blue-mid);white-space:nowrap">No More Rinsing or Refrigeration</div>
    <div class="copy dense" style="left:5px;top:26px;width:88px;height:76px"></div>
    <div class="mini" style="left:5px;top:108px;color:var(--blue-mid);font-size:2.6px">REQUEST YOUR COMPLIMENTARY TEST KIT TODAY</div>
    <div class="mini" style="left:5px;top:114px;font-size:2.8px">meridianlabs.example · 555-014-2290</div>
  </div>
  <div class="page">
    <div class="hd" style="left:5px;top:18px;font-size:2.8px;color:#1f2a37;width:48px">Skin Biopsy to Diagnose Small Fiber Neuropathy</div>
    <div class="copy" style="left:5px;top:28px;width:48px;height:22px"></div>
    <div class="photo" role="img" aria-label="Anatomical drawing of skin layers and nerve fibers" style="left:5px;top:52px;width:48px;height:34px;background:linear-gradient(#f3ead9,#dbc5a3)"></div>
    <div class="hd" style="left:58px;top:18px;font-size:2.8px;color:#1f2a37;width:36px">Small Fiber Neuropathy Testing</div>
    <div class="copy" style="left:58px;top:28px;width:36px;height:80px"></div>
    <div class="copy" style="left:5px;top:92px;width:48px;height:22px"></div>
  </div>
</div>

<!-- Row 3 -->
<div class="spread" style="left:39px;top:367px">
  <div class="page"><div class="tab" style="left:0;width:3px;top:20px;height:90px"></div></div>
  <div class="page">
    <div class="brand" style="left:5px;top:6px"><span class="dot"></span>MERIDIAN</div>
    <div class="grid" style="left:5px;top:16px;width:88px;height:10px"></div>
    <div class="grid" style="left:5px;top:32px;width:88px;height:18px"></div>
    <div class="grid" style="left:5px;top:56px;width:88px;height:12px"></div>
    <div class="grid" style="left:5px;top:72px;width:60px;height:30px"></div>
  </div>
</div>

<div class="spread" style="left:267px;top:367px">
  <div class="page">
    <div class="brand" style="left:5px;top:6px"><span class="dot"></span>MERIDIAN</div>
    <div class="grid" style="left:5px;top:16px;width:88px;height:10px"></div>
    <div class="copy dense" style="left:5px;top:30px;width:88px;height:80px"></div>
  </div>
  <div class="page">
    <div class="hd" style="left:5px;top:10px;font-size:2.8px;color:var(--blue-mid);white-space:nowrap">PHYSICIAN NOTIFICATIONS OF CRITICAL VALUES</div>
    <div class="grid blue-head" style="left:5px;top:18px;width:88px;height:32px"></div>
    <div class="grid blue-head" style="left:5px;top:54px;width:88px;height:22px"></div>
    <div class="grid blue-head" style="left:5px;top:80px;width:88px;height:14px"></div>
    <div class="copy" style="left:5px;top:98px;width:88px;height:10px"></div>
  </div>
</div>

<div class="spread" style="left:497px;top:367px">
  <div class="page"><div class="grid blue-head" style="left:5px;top:8px;width:88px;height:104px;background-color:var(--blue-mist)"></div></div>
  <div class="page"><div class="grid blue-head" style="left:5px;top:8px;width:88px;height:104px;background-color:var(--blue-mist)"></div></div>
</div>

<div class="spread" style="left:725px;top:367px">
  <div class="page"></div>
  <div class="page">
    <svg class="cover-band" viewBox="0 0 100 128" preserveAspectRatio="none"><polygon points="0,0 100,0 100,10 0,30" fill="var(--blue-dark)"/></svg>
    <span class="cover-mark"></span>
    <div class="tab" style="top:30px;height:60px"></div>
    <div class="cover-title" style="left:52px;top:44px;font-size:8px">PCR<br>PANELS</div>
    <svg class="abs" style="left:6px;top:32px" width="40" height="64" viewBox="0 0 40 64"><g fill="var(--blue-pale)" stroke="var(--white)" stroke-width="1"><circle cx="10" cy="10" r="9"/><circle cx="30" cy="10" r="9"/><circle cx="10" cy="32" r="9"/><circle cx="30" cy="32" r="9"/><circle cx="20" cy="53" r="9"/></g></svg>
    <div class="photo" role="img" aria-label="Gloved hands holding a rapid test cassette" style="left:40px;top:70px;width:55px;height:58px"></div>
  </div>
</div>

<div class="spread" style="left:950px;top:367px">
  <div class="page">
    <div class="brand" style="left:5px;top:6px"><span class="dot"></span>MERIDIAN</div>
    <div class="hd" style="left:48px;top:6px;font-size:3px;color:#1f2a37">Final Report</div>
    <div class="grid" style="left:5px;top:16px;width:88px;height:10px"></div>
    <div class="copy" style="left:5px;top:30px;width:60px;height:80px"></div>
    <div class="photo" role="img" aria-label="Microscope tissue slide images" style="left:72px;top:48px;width:22px;height:40px;background:linear-gradient(#f3d5e2,#c98aa8)"></div>
  </div>
  <div class="page">
    <svg class="cover-band" viewBox="0 0 100 128" preserveAspectRatio="none"><polygon points="0,0 100,0 100,8 0,34" fill="var(--blue-dark)"/></svg>
    <span class="cover-mark" style="left:50px"></span>
    <div class="photo lab" role="img" aria-label="Lab technician handling sample tubes" style="left:50px;top:26px;width:45px;height:102px;clip-path:polygon(30% 0,100% 0,100% 100%,0 100%)"></div>
    <div class="cover-title" style="left:5px;top:44px;font-size:5px">Pathology Testing</div>
    <div class="copy" style="left:5px;top:52px;width:38px;height:24px"></div>
  </div>
</div>

<!-- Row 4 -->
<div class="spread" style="left:39px;top:507px">
  <div class="page">
    <div class="brand" style="left:5px;top:6px"><span class="dot"></span>MERIDIAN</div>
    <div class="grid" style="left:5px;top:16px;width:88px;height:10px"></div>
    <div class="copy dense" style="left:5px;top:30px;width:88px;height:80px"></div>
  </div>
  <div class="page">
    <div class="grid blue-head" style="left:5px;top:6px;width:78px;height:114px"></div>
    <div class="vt" style="right:3px;top:10px;font-size:3.4px">METABOLITES &amp; WINDOWS OF DETECTION</div>
  </div>
</div>

<div class="spread" style="left:267px;top:507px">
  <div class="page"><div class="grid blue-head" style="left:5px;top:6px;width:88px;height:110px"></div></div>
  <div class="page">
    <div class="vt" style="left:6px;top:10px;font-size:3.6px">Blood Collection Reference Guide</div>
    <div class="vt" style="left:14px;top:88px;font-size:3px;color:var(--blue-dark)">MERIDIAN</div>
    <div class="rotate-guide" style="left:34px;top:8px;width:34px">
      <div class="swatch" style="background:#d84a3b"></div><div class="swatch" style="background:var(--yellow)"></div><div class="swatch" style="background:#7e7e7e"></div><div class="swatch" style="background:#6c3da1"></div><div class="swatch" style="background:#2c9a48"></div><div class="swatch" style="background:var(--blue-mid)"></div>
    </div>
    <div class="copy" style="left:72px;top:8px;width:22px;height:108px"></div>
    <div class="grid" style="left:34px;top:52px;width:34px;height:60px"></div>
  </div>
</div>

<div class="spread" style="left:497px;top:507px">
  <div class="page">
    <div class="grid blue-head" style="left:5px;top:8px;width:88px;height:30px"></div>
    <div class="grid" style="left:5px;top:42px;width:88px;height:16px"></div>
    <div class="grid" style="left:5px;top:62px;width:88px;height:28px"></div>
  </div>
  <div class="page">
    <div class="brand" style="left:38px;top:12px"><span class="dot"></span>MERIDIAN</div>
    <div class="hd" style="left:36px;top:20px;font-size:2.8px;color:#1f2a37;white-space:nowrap">PGX TEST MENU</div>
    <div class="grid blue-head" style="left:5px;top:28px;width:88px;height:80px"></div>
  </div>
</div>

<div class="spread" style="left:725px;top:507px">
  <div class="page">
    <div class="brand" style="left:5px;top:10px"><span class="dot"></span>MERIDIAN</div>
    <div class="hd" style="left:42px;top:14px;font-size:3px;color:#1f2a37">Final Report</div>
    <div class="grid" style="left:5px;top:22px;width:88px;height:8px"></div>
    <div class="grid blue-head" style="left:5px;top:34px;width:88px;height:70px"></div>
  </div>
  <div class="page"></div>
</div>

<div class="spread" style="left:950px;top:507px">
  <div class="page"></div>
  <div class="page">
    <div class="brand" style="left:5px;top:8px"><span class="dot"></span>MERIDIAN</div>
    <div class="hd" style="left:40px;top:6px;font-size:2.4px;width:53px;text-align:right">DERMATOLOGY<br>TEST REQUISITION FORM</div>
    <div class="grid" style="left:5px;top:16px;width:88px;height:30px"></div>
    <div class="grid" style="left:5px;top:48px;width:44px;height:60px"></div>
    <div class="copy dense" style="left:52px;top:48px;width:41px;height:60px"></div>
  </div>
</div>

<!-- Row 5 -->
<div class="spread" style="left:39px;top:647px">
  <div class="page">
    <div class="vt" style="left:3px;top:10px;font-size:3.4px">METABOLITES &amp; WINDOWS OF DETECTION</div>
    <div class="grid blue-head" style="left:14px;top:6px;width:80px;height:114px"></div>
  </div>
  <div class="page">
    <div class="brand" style="left:5px;top:6px"><span class="dot"></span>MERIDIAN</div>
    <div class="hd" style="left:34px;top:6px;font-size:2.4px;width:59px;text-align:right">TOXICOLOGY TEST REQUISITION FORM</div>
    <div class="grid" style="left:5px;top:14px;width:88px;height:22px"></div>
    <div class="copy dense" style="left:5px;top:38px;width:42px;height:76px"></div>
    <div class="grid" style="left:50px;top:38px;width:43px;height:76px"></div>
  </div>
</div>

<div class="spread" style="left:267px;top:647px">
  <div class="page">
    <div class="brand" style="left:5px;top:6px"><span class="dot"></span>MERIDIAN</div>
    <div class="grid" style="left:5px;top:16px;width:88px;height:10px"></div>
    <div class="copy dense" style="left:5px;top:30px;width:70px;height:70px"></div>
  </div>
  <div class="page">
    <div class="vt" style="left:6px;top:12px;font-size:3.4px">Specimen Collection Reference Guide</div>
    <div class="grid" style="left:30px;top:8px;width:64px;height:108px"></div>
  </div>
</div>

<div class="spread" style="left:497px;top:647px">
  <div class="page">
    <div class="brand" style="left:5px;top:6px"><span class="dot"></span>MERIDIAN</div>
    <div class="mini" style="left:5px;top:15px;color:var(--blue-dark);font-size:2.8px">Medication Summary Table</div>
    <div class="grid" style="left:5px;top:22px;width:88px;height:90px"></div>
  </div>
  <div class="page">
    <div class="brand" style="left:5px;top:6px"><span class="dot"></span>MERIDIAN</div>
    <div class="mini" style="left:5px;top:15px;color:var(--blue-dark);font-size:2.8px">Medication Summary Table</div>
    <div class="grid" style="left:5px;top:22px;width:88px;height:70px"></div>
  </div>
</div>

<div class="spread" style="left:725px;top:647px">
  <div class="page">
    <div class="brand" style="left:5px;top:10px"><span class="dot"></span>MERIDIAN</div>
    <div class="hd" style="left:36px;top:16px;font-size:3px;color:#1f2a37">Final Report</div>
    <div class="grid" style="left:5px;top:24px;width:88px;height:36px"></div>
    <div class="copy" style="left:5px;top:64px;width:88px;height:40px"></div>
  </div>
  <div class="page">
    <div class="brand" style="left:5px;top:6px"><span class="dot"></span>MERIDIAN</div>
    <div class="hd" style="left:34px;top:7px;font-size:2.4px;width:59px;text-align:right">INFECTIOUS DISEASES REQUISITION</div>
    <div class="grid" style="left:5px;top:14px;width:88px;height:104px"></div>
  </div>
</div>

<div class="spread" style="left:950px;top:647px">
  <div class="page"></div>
  <div class="page">
    <div class="brand" style="left:5px;top:6px"><span class="dot"></span>MERIDIAN</div>
    <div class="hd" style="left:34px;top:5px;font-size:2.4px;width:59px;text-align:right">GASTROINTESTINAL (GI)<br>TEST REQUISITION FORM</div>
    <div class="grid" style="left:5px;top:16px;width:88px;height:22px"></div>
    <div class="bar" style="left:5px;top:40px;width:88px;height:2px;background:var(--yellow)"></div>
    <div class="grid" style="left:5px;top:44px;width:88px;height:70px"></div>
  </div>
</div>

<!-- Row 6 -->
<div class="spread" style="left:39px;top:789px;height:130px">
  <div class="page">
    <div class="copy dense" style="left:5px;top:6px;width:88px;height:8px"></div>
    <div class="copy" style="left:5px;top:18px;width:42px;height:60px"></div>
    <div class="copy" style="left:50px;top:18px;width:43px;height:60px"></div>
    <div class="copy" style="left:5px;top:84px;width:88px;height:22px"></div>
    <div class="bar" style="left:5px;top:112px;width:88px;height:10px;background:var(--blue-mist);border:0.5px solid var(--blue-soft)"></div>
  </div>
  <div class="page">
    <div class="copy dense" style="left:5px;top:8px;width:76px;height:110px"></div>
    <div class="vt" style="right:3px;top:10px;font-size:3px">COMMON POC DRUG CROSS REACTANTS</div>
  </div>
</div>

<div class="spread" style="left:267px;top:789px;height:130px">
  <div class="page"></div>
  <div class="page">
    <svg class="cover-band" viewBox="0 0 100 130" preserveAspectRatio="none"><polygon points="0,0 100,0 100,18 0,38" fill="var(--blue-dark)"/></svg>
    <span class="cover-mark" style="left:22px"></span>
    <div class="tab" style="top:20px;height:70px"></div>
    <div class="cover-title" style="left:24px;top:42px;font-size:6.4px">PGX Testing</div>
    <div class="photo lab" role="img" aria-label="Scientist working at a microscope" style="left:0;top:58px;width:95px;height:72px;clip-path:polygon(0 14%,100% 0,100% 100%,0 100%)"></div>
  </div>
</div>

<div class="spread" style="left:497px;top:789px;height:130px">
  <div class="page"></div>
  <div class="page">
    <svg class="cover-band" viewBox="0 0 100 130" preserveAspectRatio="none"><polygon points="0,0 100,0 100,20 0,38" fill="var(--blue-dark)"/></svg>
    <span class="cover-mark" style="left:22px"></span>
    <div class="tab" style="top:20px;height:70px"></div>
    <div class="cover-title" style="left:36px;top:42px;font-size:6px">Culture Testing</div>
    <div class="photo warm" role="img" aria-label="Smiling patient talking with her doctor" style="left:0;top:58px;width:95px;height:72px;clip-path:polygon(0 10%,100% 0,100% 100%,0 100%)"></div>
  </div>
</div>

<div class="spread" style="left:725px;top:789px;height:130px">
  <div class="page">
    <div class="brand" style="left:5px;top:14px"><span class="dot"></span>MERIDIAN</div>
    <div class="hd" style="left:34px;top:10px;font-size:2.4px;width:59px;text-align:right">INFECTIOUS DISEASES REQUISITION</div>
    <div class="grid" style="left:5px;top:22px;width:88px;height:100px"></div>
  </div>
  <div class="page">
    <svg class="cover-band" viewBox="0 0 100 130" preserveAspectRatio="none"><polygon points="0,0 100,0 100,10 0,34" fill="var(--blue-dark)"/></svg>
    <span class="cover-mark"></span>
    <div class="hd" style="left:10px;top:40px;font-size:4.6px;color:var(--blue-mid);text-align:right;width:84px">Respiratory Pathogen<br>Testing (QPCR)</div>
    <div class="copy" style="left:10px;top:54px;width:84px;height:14px"></div>
    <div class="bar" style="left:10px;top:72px;width:36px;height:12px;background:var(--white);border:0.5px solid var(--line);z-index:2"></div>
    <div class="photo lab" role="img" aria-label="Doctor viewing a chest scan on a tablet" style="left:30px;top:72px;width:65px;height:58px;clip-path:polygon(30% 0,100% 0,100% 100%,0 100%)"></div>
  </div>
</div>

<div class="spread" style="left:950px;top:789px;height:130px">
  <div class="page" style="background:var(--blue-dark)">
    <div class="photo lab" role="img" aria-label="Laboratory staff at work" style="left:0;top:0;width:100%;height:56px"></div>
    <div class="contact-word" style="left:24px;top:44px">CONTACT</div>
    <div class="mini" style="left:24px;top:58px;color:var(--white);font-size:2.4px">555-014-2290 · info@meridianlabs.example</div>
  </div>
  <div class="page">
    <svg class="cover-band" viewBox="0 0 100 130" preserveAspectRatio="none"><polygon points="0,0 100,0 100,30 0,80" fill="var(--blue-dark)"/><polygon points="0,80 100,30 100,36 0,86" fill="var(--blue-mid)"/></svg>
    <span class="abs" style="left:18px;top:96px;width:9px;height:9px;border-radius:50%;border:1px solid var(--blue-dark)"></span>
    <div class="brand" style="left:12px;top:108px;font-size:3.6px">MERIDIAN LABS</div>
  </div>
</div>

</body>
</html>
```